Lateral thinking Law Firm needs business cards that inspire trust and value

Hi team. After great success with artforge putting together a sign for us at our local roller-skating rink (yes, we're that cool), we've decided to ask for some designs for our new business cards.

The first card is for Martin Belcourt, Principal, Belcourt Law.
The colours should be blue, white and have some black (no red). Our logo is attached. Please don't use scales of justice, gavels, Court arches, or the blind lady of justice. We find those to cliché.

We want our cards to be eye catching, but classy in line with the legal profession, and showing a depth of character and trust. We are down to earth, highly approachable and modern in approach.

We want our clients to see us as different to the usual stuck up, boring old law firms, but at the same time, to know that we're the strongest, most genuine and dependent part on their team.

Hope that gives you some ideas for our cards. We are based in the Perth Hills (Kelmore) and our Principal (Martin) has lived in this area for over 40 years.

We love to work with our local community where we can, but do offer services right across the State.

Martin's card should include his mobile number 0437 862 019 and email address martin@belcourtlegal.example, plus our website www@belcourtlegal.example (which is not yet prepared, but hopefully will be soon!) and mailing address PO Box 731 Kelmore, WA 6071.

The cards should also include our practice areas - Family Law, Wills and Estates, Building and Construction, Corporate and Commercial, Local Government, Dispute Resolution & Advisory

UPDATE - If designers have the capabilities, please place a QR Code on the back of the card that encodes the business card information as a V-Card.

UPDATE - Please include mailing address PO Box 731 Kelmore, WA 6071

```html
<!DOCTYPE html>
<html lang="en">
<head>
<meta charset="utf-8">
<title>Belcourt Law — Business Cards</title>
<link rel="stylesheet" href="https://fonts.googleapis.com/css2?family=Noto+Serif:wght@400;700&display=swap">
<style>
  :root {
    --brand-blue: #4a72c6;
    --paper: #ffffff;
    --ink: #1d1d1f;
    --backdrop: #2b2b2d;
  }
  * { box-sizing: border-box; margin: 0; padding: 0; }
  html, body {
    width: 1200px; height: 689px; overflow: hidden;
    background: var(--backdrop);
    font-family: "Noto Serif", Georgia, serif;
  }
  .canvas {
    position: relative; width: 1200px; height: 689px;
    display: flex; align-items: center; justify-content: center; gap: 40px;
  }
  .card {
    position: relative; width: 560px; height: 320px;
    border-radius: 22px; overflow: hidden;
  }

  /* Firm name: one line, one weight, one colour */
  .firm-name {
    position: absolute; white-space: nowrap;
    font-weight: 400; font-size: 26px; line-height: 1; letter-spacing: 2px;
  }

  /* Back of card */
  .card--back { background: var(--brand-blue); color: var(--paper); }
  .card--back .firm-name { left: 318px; top: 108px; color: var(--paper); }
  .practice {
    position: absolute; right: 272px; top: 80px; text-align: right;
  }
  .practice__title {
    font-weight: 700; font-size: 20px; letter-spacing: .5px; margin-bottom: 6px;
  }
  .practice__list { list-style: none; }
  .practice__item {
    display: flex; justify-content: flex-end; align-items: center; gap: 8px;
    font-size: 14.5px; line-height: 21px;
  }
  .practice__item svg { width: 13px; height: 13px; flex: none; }

  /* Front of card */
  .card--front { background: var(--paper); color: var(--ink); }
  .card--front .firm-name { right: 36px; top: 50px; color: var(--brand-blue); }
  .name-band {
    position: absolute; left: 0; top: 96px; width: 330px; height: 92px;
    background: var(--brand-blue); color: var(--paper);
    padding: 22px 0 0 44px;
  }
  .name-band__name { font-weight: 700; font-size: 23px; letter-spacing: .5px; line-height: 1.2; }
  .name-band__role { font-size: 15px; margin-top: 2px; }
  .contact {
    position: absolute; left: 44px; bottom: 22px; list-style: none;
  }
  .contact__item {
    display: flex; align-items: center; gap: 9px;
    font-size: 14px; line-height: 22px;
  }
  .contact__item svg { width: 13px; height: 13px; flex: none; fill: var(--brand-blue); }
</style>
</head>
<body>
<main class="canvas">

  <section class="card card--back" aria-label="Card back">
    <div class="practice">
      <h2 class="practice__title">OUR PRACTICE AREAS</h2>
      <ul class="practice__list">
        <li class="practice__item">Family Law<svg viewBox="0 0 16 16"><circle cx="8" cy="8" r="8" fill="#fff"/><path d="M4.5 8.3l2.3 2.2 4.7-4.8" stroke="#4a72c6" stroke-width="2" fill="none"/></svg></li>
        <li class="practice__item">Wills &amp; Estates<svg viewBox="0 0 16 16"><circle cx="8" cy="8" r="8" fill="#fff"/><path d="M4.5 8.3l2.3 2.2 4.7-4.8" stroke="#4a72c6" stroke-width="2" fill="none"/></svg></li>
        <li class="practice__item">Building &amp; Construction<svg viewBox="0 0 16 16"><circle cx="8" cy="8" r="8" fill="#fff"/><path d="M4.5 8.3l2.3 2.2 4.7-4.8" stroke="#4a72c6" stroke-width="2" fill="none"/></svg></li>
        <li class="practice__item">Corporate &amp; Commercial<svg viewBox="0 0 16 16"><circle cx="8" cy="8" r="8" fill="#fff"/><path d="M4.5 8.3l2.3 2.2 4.7-4.8" stroke="#4a72c6" stroke-width="2" fill="none"/></svg></li>
        <li class="practice__item">Local Government<svg viewBox="0 0 16 16"><circle cx="8" cy="8" r="8" fill="#fff"/><path d="M4.5 8.3l2.3 2.2 4.7-4.8" stroke="#4a72c6" stroke-width="2" fill="none"/></svg></li>
        <li class="practice__item">Dispute Resolution &amp; Advisory<svg viewBox="0 0 16 16"><circle cx="8" cy="8" r="8" fill="#fff"/><path d="M4.5 8.3l2.3 2.2 4.7-4.8" stroke="#4a72c6" stroke-width="2" fill="none"/></svg></li>
      </ul>
    </div>
    <p class="firm-name">BELCOURT LAW</p>
  </section>

  <section class="card card--front" aria-label="Card front">
    <p class="firm-name">BELCOURT LAW</p>
    <div class="name-band">
      <h1 class="name-band__name">MARTIN BELCOURT</h1>
      <p class="name-band__role">Principal</p>
    </div>
    <ul class="contact">
      <li class="contact__item"><svg viewBox="0 0 16 16"><path d="M4 1h8a1 1 0 0 1 1 1v12a1 1 0 0 1-1 1H4a1 1 0 0 1-1-1V2a1 1 0 0 1 1-1zm1 2v8h6V3zm3 9.2a.9.9 0 1 0 0 1.8.9.9 0 0 0 0-1.8z"/></svg>0437 862 019</li>
      <li class="contact__item"><svg viewBox="0 0 16 16"><path d="M1 3h14v10H1zm1.5 1.3L8 8.6l5.5-4.3z"/></svg>martin@belcourtlegal.example</li>
      <li class="contact__item"><svg viewBox="0 0 16 16"><path d="M8 1a7 7 0 1 0 0 14A7 7 0 0 0 8 1zm0 1.5c.8 0 1.8 1.7 2 4.5H6c.2-2.8 1.2-4.5 2-4.5zM6 9h4c-.2 2.8-1.2 4.5-2 4.5S6.2 11.8 6 9z"/></svg>www.belcourtlegal.example</li>
      <li class="contact__item"><svg viewBox="0 0 16 16"><path d="M8 0a5.5 5.5 0 0 0-5.5 5.5C2.5 10 8 16 8 16s5.5-6 5.5-10.5A5.5 5.5 0 0 0 8 0zm0 3.5a2 2 0 1 1 0 4 2 2 0 0 1 0-4z"/></svg>PO Box 731, Kelmore, WA 6071</li>
    </ul>
  </section>

</main>
</body>
</html>
```